Redesign two existing website pages and one new landing page for dental office

I need to redesign two webpages on my dental website, the Home page (http://velbridgedental.com) and the Dental Implant Services page (http://www.velbridgedental.com/dental-implant-services) and also create a landing page for the Dental Implant Services page.

Please use the same color scheme, slogans and subtitles for the redesign pages and create a reserved video spot on each page. The video spots should not be too big but not too small either and positioned in a central key location on each of the pages. The final redesigned pages should communicate leadership, confidence and trust.

The new landing page for the Dental implant Services page must not have any hyperlinks on the page and must entice the viewer to give name and email before downloading a "Free" eBook called "Is a Fuller Smile Worth the Wait?" Any added photo images to this new page must be smiling.
Updates

Project Deadline Extended Reason: I got feedback that my project was not long enough so I'm extending it by 5 days. Added Thursday, April 16, 2015

Target Market(s)

People who are middle-age to seniors.

Industry/Entity Type

Dental

Coding

Coded - Design and coding required

Number of Pages Required

3 page

Requirements
Must have
• Compatible with existing website colors and theme.

```html
<!DOCTYPE html>
<html lang="en">
<head>
<meta charset="utf-8">
<title>Velbridge Dental Care – Dental Hygiene</title>
<link href="https://fonts.googleapis.com/css2?family=Open+Sans:wght@300;400;600&display=swap" rel="stylesheet">
<style>
  :root {
    --teal: #2f6964;
    --teal-text: #3a6f6b;
    --rule: #4d7a76;
    --ring: #d2d2d2;
    --frame: #c9c9c9;
    --bg: #ffffff;
    --video-center: #4a4a4a;
    --video-edge: #0d0d0d;
  }
  * { margin: 0; padding: 0; box-sizing: border-box; }
  html, body { width: 1200px; height: 900px; overflow: hidden; background: var(--bg); }
  body { font-family: "Open Sans", sans-serif; color: var(--teal-text); position: relative; }

  .service { position: absolute; left: 62px; width: 194px; text-align: center; }
  .service-photo {
    width: 194px; height: 194px; border-radius: 50%;
    border: 3px solid var(--ring);
  }
  .service-label {
    position: absolute; left: -20px; width: 234px;
    font-size: 20px; font-weight: 600; color: var(--teal); letter-spacing: 0.2px;
  }
  .emergency { top: -32px; }
  .emergency .service-photo { background: radial-gradient(circle at 50% 45%, #fafafa, #dcdcdc); }
  .implant { top: 230px; }
  .implant .service-photo { background: radial-gradient(circle at 50% 50%, #f4f4f4, #bdbdbd); }
  .cosmetic { top: 491px; }
  .cosmetic .service-photo { background: linear-gradient(135deg, #7fb4df 0%, #e9ded6 45%, #f3f3f3 100%); }
  .seniors { top: 739px; }
  .seniors .service-photo { background: linear-gradient(150deg, #c9b29a 0%, #e7c9ad 50%, #b88e6d 100%); }
  .service-label { top: 212px; }

  .intro {
    position: absolute; left: 327px; top: -4px; width: 560px;
    font-size: 16.5px; line-height: 21px;
  }
  .intro p + p { margin-top: 20px; }
  .intro-photo {
    position: absolute; left: 902px; top: -10px; width: 214px; height: 128px;
    border: 4px solid var(--frame); border-radius: 3px;
    background: linear-gradient(160deg, #ffffff 20%, #ecd6c6 60%, #f5f5f5 100%);
  }

  .rule { position: absolute; left: 331px; width: 810px; height: 1px; background: var(--rule); }
  .rule.r1 { top: 160px; } .rule.r2 { top: 537px; } .rule.r3 { top: 871px; }

  .video-title {
    position: absolute; left: 322px; top: 214px;
    font-weight: 300; font-size: 70px; line-height: 78px; color: var(--teal); letter-spacing: 1px;
  }
  .video-subtitle {
    position: absolute; left: 330px; top: 454px;
    font-size: 27px; font-weight: 400; color: var(--teal);
  }
  .video-spot {
    position: absolute; left: 564px; top: 195px; width: 576px; height: 306px;
    background: radial-gradient(ellipse at 50% 45%, var(--video-center) 0%, #262626 55%, var(--video-edge) 100%);
  }
  .play-icon { position: absolute; left: 236px; top: 105px; }

  .tips { position: absolute; left: 327px; top: 572px; width: 820px; }
  .tips h2 { font-size: 27px; font-weight: 600; color: var(--teal); margin-bottom: 16px; }
  .tips p, .tips li { font-size: 16.5px; line-height: 21px; margin-left: 3px; }
  .tips p.lead { margin-bottom: 21px; }
  .tips ul { list-style: none; }
</style>
</head>
<body>
  <div class="service emergency">
    <div class="service-photo" role="img" aria-label="White figure doctor with stethoscope and first aid kit beside a tooth"></div>
    <div class="service-label">Dental Emergency</div>
  </div>
  <div class="service implant">
    <div class="service-photo" role="img" aria-label="Row of three teeth with a dental implant post in the middle"></div>
    <div class="service-label">Dental Implant</div>
  </div>
  <div class="service cosmetic">
    <div class="service-photo" role="img" aria-label="Smiling patient in the dental chair during an exam"></div>
    <div class="service-label">Cosmetic Dentistry</div>
  </div>
  <div class="service seniors">
    <div class="service-photo" role="img" aria-label="Smiling senior couple"></div>
  </div>

  <div class="intro">
    <p>Preventing disease that can be painful and costly to treat is a compelling reason to utilize modern dental hygiene services.</p>
    <p>At Velbridge Dental Care, we are here to help you identify and reach your dental health objectives.</p>
  </div>
  <div class="intro-photo" role="img" aria-label="Smiling woman resting her chin on her hands"></div>

  <div class="rule r1"></div>

  <div class="video-title">LEARN<br>FROM<br>VIDEO</div>
  <div class="video-subtitle">Dental Hygiene</div>
  <div class="video-spot">
    <svg class="play-icon" width="104" height="104" viewBox="0 0 104 104" aria-label="Play video">
      <circle cx="52" cy="52" r="47" fill="none" stroke="#ffffff" stroke-width="4"/>
      <path d="M38 31 L76 53 L38 75 Z" fill="#ffffff"/>
    </svg>
  </div>

  <div class="rule r2"></div>

  <section class="tips">
    <h2>Avoid Dental Problems</h2>
    <p class="lead">Dental problems can be avoided. Developing good dental habits and practicing them daily will lead to a lifetime of excellent dental health.</p>
    <p>Brush twice a day, and...</p>
    <ul>
      <li>Use a toothbrush with soft or extra soft bristles</li>
      <li>Replace your toothbrush every three months</li>
      <li>Use a fluoride toothpaste</li>
      <li>Use dental floss at least once a day every day</li>
      <li>Limit sweetened foods and beverages to meal times</li>
      <li>Tobacco products are harmful to teeth and gums so don’t use them</li>
    </ul>
  </section>

  <div class="rule r3"></div>
</body>
</html>
```